Medical Practice needs a Letterhead Design

We need a clean, modern letterhead design for our stem cell medical practice.

Industry/Entity Type

Medical

```html
<!DOCTYPE html>
<html lang="en">
<head>
<meta charset="utf-8">
<title>Harborview Practice Letterhead</title>
<link rel="stylesheet" href="https://fonts.googleapis.com/css2?family=Lora:wght@400;600&family=Lato:wght@400;700&display=swap">
<style>
  :root {
    --backdrop: #1c1d1f;
    --paper: #ffffff;
    --navy: #1f3a4d;
    --ink: #4a4d50;
    --muted: #8a8d90;
    --rule: #c9cbcd;
    --signature: #dedfe0;
  }
  * { margin: 0; padding: 0; box-sizing: border-box; }
  html, body { width: 1200px; height: 800px; overflow: hidden; background: var(--backdrop); }
  .letterhead {
    position: absolute; left: 330px; top: 20px; width: 540px; height: 760px;
    background: var(--paper); color: var(--ink);
    font-family: "Lora", Georgia, serif; font-size: 10.5px; line-height: 1.55;
    padding: 40px 64px 0 64px;
  }
  .brand { display: flex; align-items: center; justify-content: center; }
  .brand-name {
    font-family: "Lora", Georgia, serif; font-weight: 400; font-size: 20px;
    color: var(--ink); letter-spacing: 0.5px;
  }
  .recipient { margin-top: 124px; }
  .recipient-name { font-family: "Lato", Arial, sans-serif; font-weight: 700; color: var(--navy); letter-spacing: 0.5px; }
  .greeting { margin-top: 14px; }
  .body-copy p { margin-top: 14px; text-align: justify; }
  .closing { margin-top: 16px; }
  .signature {
    margin-top: 10px; width: 150px; height: 46px; border-radius: 4px;
    background: linear-gradient(90deg, var(--signature), #f2f2f2);
  }
  .signer-name { font-family: "Lato", Arial, sans-serif; font-weight: 700; color: var(--navy); margin-top: 4px; }
  .signer-role { font-family: "Lato", Arial, sans-serif; color: var(--ink); }
  .footer-contact {
    position: absolute; right: 64px; bottom: 70px; text-align: right;
    font-family: "Lato", Arial, sans-serif; font-size: 7px; line-height: 1.6; color: var(--muted);
  }
  .footer-rule { position: absolute; height: 1px; background: var(--rule); }
  .footer-rule.left { left: 64px; bottom: 40px; width: 60px; }
  .footer-rule.right { right: 64px; bottom: 40px; width: 60px; }
</style>
</head>
<body>
  <main class="letterhead">
    <header class="brand">
      <span class="brand-name">Harborview Practice</span>
    </header>

    <section class="recipient">
      <div>Sr.</div>
      <div class="recipient-name">MARCO DELGADO</div>
      <div>Web Master</div>
      <div>City</div>
    </section>

    <p class="greeting">Lorem ipsum dolor sit amet...</p>

    <section class="body-copy">
      <p>Consetetur sadipscing elitr, sed diam nonumy eirmod tempor invidunt ut labore et dolore magna aliquyam erat, sed diam voluptua. At vero eos et accusam et justo duo dolores et ea rebum. Stet clita kasd gubergren, ipsum dolor sit amet. Lorem ipsum dolor sit amet, consetetur sadipscing elitr, sed diam nonumy eirmod tempor invidunt ut labore et dolore magna aliquyam erat, sed diam voluptua, no sea takimata sanctus est Lorem ipsum dolor sit amet, consetetur sadipscing elitr, sed diam nonumy eirmod tempor invidunt ut labore et dolore magna aliquyam erat, sed diam voluptua.</p>
      <p>Sed diam nonumy eirmod tempor invidunt ut labore et dolore magna aliquyam erat, sed diam voluptua. At vero eos et accusam et justo duo dolores et ea rebum. Stet clita kasd gubergren, no sea takimata sanctus est. Sed diam nonumy eirmod tempor invidunt ut labore et dolore magna aliquyam erat, sed diam voluptua.</p>
      <p>At vero eos et accusam et justo duo dolores et ea rebum. Stet clita kasd gubergren, no sea takimata sanctus est Lorem ipsum dolor sit amet, eirmod tempor invidunt ut labore et dolore magna aliquyam erat, sed diam voluptua.</p>
    </section>

    <p class="closing">Lorem ipsum dolor</p>
    <div class="signature" role="img" aria-label="Handwritten signature"></div>
    <div class="signer-name">ELENA WARD</div>
    <div class="signer-role">Manager</div>

    <footer class="footer-contact">
      <div>www.harborviewpractice.com &nbsp; hello@harborviewpractice.com</div>
      <div>Tel 555 0148 2260</div>
      <div>42 Harbor Lane, Suite 4</div>
      <div>City, State, Country</div>
    </footer>
    <span class="footer-rule left"></span>
    <span class="footer-rule right"></span>
  </main>
</body>
</html>
```